Leap Past Harvest Moon 21 day Challenge

We are having a Leap Past Harvest Moon Challenge at our fitness studio. We need a poster design using the template attached as a reference. I have also included our Zorbelle logo to put on the poster. Please DO NOT use the graphics in the flyer as we are expecting something much better :-)

-Size needed 11x17 with bleeding for printing

-We need this made in Photoshop (CS3 friendly) or at least delivered in PS as we might change some text or re-arrange the design later on.

-We need this in layers.

Fitness

```html
<!DOCTYPE html>
<html lang="en">
<head>
<meta charset="utf-8">
<title>Zorbelle Boot Camps – Leap Past Harvest Moon</title>
<link rel="stylesheet" href="https://fonts.googleapis.com/css2?family=Oswald:wght@500;700&family=Roboto+Condensed:ital,wght@0,400;0,700;1,700&display=swap">
<style>
  :root {
    --paper: #f4f4f4;
    --mist: #cfcfcf;
    --charcoal: #2b2b2b;
    --ink: #151515;
    --red: #e02b2b;
    --red-deep: #b81c1c;
    --white: #ffffff;
    --grey-text: #9a9a9a;
  }
  * { margin: 0; padding: 0; box-sizing: border-box; }
  html, body { width: 778px; height: 1200px; overflow: hidden; }
  body { font-family: "Roboto Condensed", sans-serif; background: var(--charcoal); }

  .poster {
    position: relative;
    width: 778px;
    height: 1200px;
    overflow: hidden;
    background: linear-gradient(180deg, var(--paper) 0%, #e6e6e6 30%, var(--mist) 44%, #6a6a6a 52%, var(--charcoal) 60%, var(--ink) 100%);
  }

  .brand {
    position: absolute; top: 18px; left: 0; width: 100%;
    text-align: center; z-index: 3;
  }
  .brand-name {
    display: inline-flex; align-items: center; gap: 12px;
    font-family: "Oswald", sans-serif; font-weight: 700;
    font-size: 46px; line-height: 1; letter-spacing: 2px;
    color: var(--ink); text-transform: uppercase;
  }
  .brand-mark { width: 22px; height: 22px; background: var(--red); }
  .brand-tagline {
    margin-top: 6px;
    font-family: "Oswald", sans-serif; font-weight: 500;
    font-size: 15px; letter-spacing: 3px; color: var(--ink);
  }

  .hero-photo {
    position: absolute; left: 120px; top: 110px; width: 540px; height: 560px;
    background: radial-gradient(ellipse 60% 55% at 50% 48%, rgba(140,112,98,0.55) 0%, rgba(120,100,90,0.3) 50%, rgba(120,100,90,0) 100%);
    z-index: 1;
  }

  .bands { position: absolute; inset: 0; z-index: 2; }

  .tilt { position: absolute; transform: rotate(-3.7deg); transform-origin: center; white-space: nowrap; }

  .headline {
    left: 30px; top: 662px; width: 720px; height: 64px;
    font-family: "Oswald", sans-serif; font-weight: 700;
    font-size: 54px; line-height: 64px; color: var(--red);
    text-transform: uppercase; text-align: center;
    font-style: italic; z-index: 3;
  }
  .headline .on-red { color: var(--white); }
  .subhead {
    left: 0; top: 760px; width: 778px; height: 50px;
    font-family: "Oswald", sans-serif; font-weight: 700;
    font-size: 34px; line-height: 50px; color: var(--charcoal);
    text-transform: uppercase; text-align: center; z-index: 3;
  }
  .promise {
    left: 0; top: 820px; width: 778px; height: 88px;
    font-family: "Oswald", sans-serif; font-weight: 700;
    font-size: 44px; line-height: 88px; color: var(--white);
    text-transform: uppercase; text-align: center; z-index: 3;
  }
  .promise .big-number { font-size: 84px; vertical-align: -6px; }

  .benefits {
    position: absolute; left: 82px; top: 956px; width: 680px;
    list-style: none; z-index: 3;
  }
  .benefits li {
    position: relative; padding-left: 34px; margin-bottom: 7px;
    font-size: 16px; line-height: 19px; color: var(--white); white-space: nowrap;
  }
  .benefits svg { position: absolute; left: 0; top: 1px; width: 20px; height: 18px; }

  .offer {
    position: absolute; left: 82px; top: 1058px; z-index: 3;
    font-weight: 700; font-size: 25px; line-height: 30px; color: var(--red);
  }

  .urgency {
    left: 130px; top: 1112px; width: 620px;
    font-weight: 700; font-style: italic; font-size: 19px; line-height: 23px;
    color: var(--white); text-transform: uppercase; text-align: center; z-index: 3;
  }

  .testimonial {
    position: absolute; right: 36px; top: 1166px; z-index: 3;
    text-align: right; font-size: 13px; line-height: 15px; color: var(--grey-text);
    font-style: italic;
  }
</style>
</head>
<body>
<main class="poster">

  <header class="brand">
    <div class="brand-name"><span class="brand-mark"></span>Zorbelle Boot Camps</div>
    <div class="brand-tagline">THE ULTIMATE FITNESS SOLUTION</div>
  </header>

  <div class="hero-photo" role="img" aria-label="Photo of an athlete after a hard workout, hands on head"></div>

  <svg class="bands" width="778" height="1200" viewBox="0 0 778 1200" aria-hidden="true">
    <polygon points="585,638 778,626 778,700 585,712" fill="var(--red)"/>
    <polygon points="0,676 585,638 585,712 0,750" fill="var(--ink)"/>
    <polygon points="0,780 778,730 778,790 0,840" fill="var(--white)"/>
    <polygon points="0,846 778,796 778,890 0,940" fill="var(--red)"/>
    <polygon points="0,934 778,884 778,890 0,940" fill="var(--red-deep)"/>
    <polygon points="120,1122 778,1090 778,1160 120,1180" fill="#1e1e1e"/>
  </svg>

  <h1 class="tilt headline">Leap Past Harvest <span class="on-red">Moon</span></h1>
  <h2 class="tilt subhead">Discover the secret to a</h2>
  <p class="tilt promise">Beach ready body in <span class="big-number">21</span> days</p>

  <ul class="benefits">
    <li><svg viewBox="0 0 20 18"><path d="M2 9 L8 15 L18 2" fill="none" stroke="var(--red)" stroke-width="4"/></svg>8 total training sessions designed to incinerate fat off your midsection, thighs, and arms</li>
    <li><svg viewBox="0 0 20 18"><path d="M2 9 L8 15 L18 2" fill="none" stroke="var(--red)" stroke-width="4"/></svg>21 days of nutritional guidance, including delicious recipes</li>
    <li><svg viewBox="0 0 20 18"><path d="M2 9 L8 15 L18 2" fill="none" stroke="var(--red)" stroke-width="4"/></svg>A Success Session to map out your individual plan for success</li>
    <li><svg viewBox="0 0 20 18"><path d="M2 9 L8 15 L18 2" fill="none" stroke="var(--red)" stroke-width="4"/></svg>Your very own Personal Accountability Coach to ensure you get results</li>
  </ul>

  <p class="offer">You get all this—a $399 value—for ONLY $99!</p>

  <p class="tilt urgency">Hurry! Space is limited to only 20 participants!!!<br>Claim your spot now: website and phone number</p>

  <blockquote class="testimonial">I've never been more fit in my life—at age 41!<br>–Marisol Quenby</blockquote>

</main>
</body>
</html>
```